New Flyer Design Project - for sale units at The Lodge phase 3

on attached the A2 is full kitchen 1 bedroom, the A3 is gally kitchen and the B2 is the the 2 bedroom, on attached pictures the room with 2 queen beds is only for the 2 bedroom

This is going to be used to sale the units (real estate sale) so the layout could possibly be text and then pictures maybe 1 bedroom on one side and 2 on the back?

Experience the Modern Luxury of the New Phase 3 Building of the
Lodge at Harper's Landing

* Opening Spring 2019

* America's #17 Family Resort; Tennessee's Only Ranked Resort

1 Bedroom Bunk Suite (Galley Kitchen) - $199,000; Sleeps 6

* Private King Master Bedroom

* Bunk Bed Galley

* Granite Counters Throughout

* Fully Furnished with Custom Furnishings

* Private Balcony

* Equipped Galley Kitchen

* In Unit Laundry

* Queen Sleeper Sofa

1 Bedroom Bunk Suite (Full Kitchen) - $209,000; Sleeps 6

* Bunk Bed Galley

* Granite Counters throughout

* Equipped Full Kitchen

* Completely Furnished with Custom Furnishings

* Private Balcony

* In Unit Laundry

* Queen Sleeper Sofa

2 Bedroom Bunk Suite (Full Kitchen) - $249,000; Sleeps 10

* Private King Master Bedroom with On-Suite Bathroom

* Two Queen Bedroom

* Bunk Bed Galley

* Full Kitchen

* Private Balcony

* In Unit Laundry

* Queen Sleeper Sofa

Target Market(s)

people wanting to buy units in phase 3 of The Lodge at Harper's Landing

Industry/Entity Type

Real Estate Development

Requirements
Must have
• attached text to describe units and price
• pictures and layouts
• Contact Dale Fenton
• 865-555-0172 Dale@bluecedarretreats.example
Nice to have
• brand and logo
Should not have
• it should not be plain this is m ore of a luxury project

```html
<!DOCTYPE html>
<html lang="en">
<head>
<meta charset="utf-8">
<title>The Lodge Phase 3 Sales Flyer</title>
<link href="https://fonts.googleapis.com/css2?family=Barlow+Semi+Condensed:wght@400;500;600;700&family=Lobster+Two:ital,wght@1,700&family=Roboto:wght@400;500;700&display=swap" rel="stylesheet">
<style>
  :root {
    --backdrop: #2f2f31;
    --teal: #5f8b97;
    --teal-text: #4f7f8c;
    --gold: #d99c55;
    --brown: #6d5440;
    --brown-dark: #5a4434;
    --cream: #fdfcf8;
    --slate: rgba(62, 66, 72, 0.86);
    --plan-bg: #efe9de;
    --white: #ffffff;
  }
  * { box-sizing: border-box; margin: 0; padding: 0; }
  html, body { width: 1200px; height: 776px; overflow: hidden; }
  body {
    background: var(--backdrop);
    font-family: "Barlow Semi Condensed", "Arial Narrow", sans-serif;
    position: relative;
  }
  .page {
    position: absolute;
    top: 30px;
    width: 540px;
    height: 716px;
    overflow: hidden;
  }
  .page--front { left: 40px; background: var(--cream); }
  .page--back { left: 620px; }

  /* front */
  .hero-photo {
    position: absolute; inset: 0 0 auto 0; height: 330px;
    background: linear-gradient(160deg, #c9cda4 0%, #8f9a6c 35%, #5c6354 65%, #3d4a55 100%);
  }
  .headline-box {
    position: absolute; left: 50px; top: 110px; width: 440px;
    padding: 16px 18px;
    background: var(--slate);
    border: 3px solid var(--white);
    color: var(--white);
    text-align: center;
    font-weight: 500;
    font-size: 23px;
    line-height: 1.3;
    letter-spacing: 0.3px;
  }
  .photo-strip {
    position: absolute; left: 14px; right: 14px; top: 300px; height: 118px;
    background: var(--gold);
    display: flex; gap: 6px; padding: 8px;
  }
  .photo-strip .thumb { flex: 1; }
  .thumb--bedroom { background: linear-gradient(150deg, #dfe1c6, #8b8e73 60%, #5d5447); }
  .thumb--dining { background: linear-gradient(150deg, #cfc9b8, #7a6f5e 55%, #3f3832); }
  .thumb--kitchen { background: linear-gradient(150deg, #d6d4cc, #7d8a92 55%, #2f2f33); }
  .thumb--bath { background: linear-gradient(150deg, #f1efe6, #c8c4a8 55%, #5a4636); }
  .opening-tab {
    position: absolute; left: 110px; top: 418px; width: 320px; height: 52px;
    background: var(--brown);
    clip-path: polygon(0 0, 100% 0, 94% 100%, 6% 100%);
    display: flex; align-items: center; justify-content: center;
    font-family: "Lobster Two", cursive;
    font-style: italic; font-weight: 700;
    font-size: 30px; color: var(--gold);
  }
  .ranking {
    position: absolute; left: 0; right: 0; top: 492px;
    text-align: center;
    font-family: "Lobster Two", cursive;
    font-style: italic; font-weight: 700;
    font-size: 19px; color: var(--teal-text);
  }
  .contact-band {
    position: absolute; left: 0; right: 0; bottom: 0; height: 170px;
    background: var(--brown);
    color: var(--white);
  }
  .contact {
    position: absolute; left: 40px; top: 48px;
    font-family: "Roboto", sans-serif;
  }
  .contact__label { font-size: 18px; }
  .contact__name { font-size: 22px; font-weight: 700; margin-top: 2px; white-space: nowrap; }
  .contact__email { font-size: 18px; margin-top: 6px; }
  .brand {
    position: absolute; right: 30px; top: 22px;
    display: flex; align-items: center; gap: 10px;
    font-family: "Roboto", sans-serif;
    font-weight: 700; font-size: 24px; color: var(--gold);
  }
  .brand__mark { width: 20px; height: 20px; border-radius: 50%; background: var(--gold); }

  /* back */
  .unit {
    position: absolute; left: 0; right: 0; height: 239px;
  }
  .unit--galley { top: 0; background: var(--teal); }
  .unit--full { top: 239px; background: var(--gold); }
  .unit--two { top: 478px; height: 238px; background: var(--brown); }
  .unit__number {
    position: absolute; left: 14px; top: 40px;
    font-family: "Roboto", sans-serif;
    font-weight: 700; font-size: 150px; line-height: 1;
    color: rgba(255, 255, 255, 0.13);
  }
  .floor-plan {
    position: absolute; left: 70px; top: 22px; width: 250px; height: 195px;
    border: 5px solid var(--white);
    background: linear-gradient(135deg, var(--plan-bg), #d8cdbb);
  }
  .unit__details {
    position: absolute; left: 332px; top: 14px; width: 200px;
    color: var(--white);
  }
  .unit__title { font-size: 15px; font-weight: 700; line-height: 1.12; }
  .unit__price { font-size: 15px; font-weight: 700; line-height: 1.12; margin-bottom: 4px; }
  .unit__features { list-style: none; font-size: 12px; line-height: 1.15; }
  .unit__features li { padding-left: 9px; position: relative; }
  .unit__features li::before { content: "•"; position: absolute; left: 0; }
</style>
</head>
<body>

<section class="page page--front">
  <div class="hero-photo" role="img" aria-label="Photo of a furnished suite bedroom with two beds"></div>
  <h1 class="headline-box">Experience the Modern Luxury of the New Phase 3 Building of the Lodge at Harper's Landing</h1>

  <div class="photo-strip">
    <div class="thumb thumb--bedroom" role="img" aria-label="Photo of the king master bedroom"></div>
    <div class="thumb thumb--dining" role="img" aria-label="Photo of the dining and living area"></div>
    <div class="thumb thumb--kitchen" role="img" aria-label="Photo of the kitchen with granite counters"></div>
    <div class="thumb thumb--bath" role="img" aria-label="Photo of the bathroom vanity"></div>
  </div>

  <div class="opening-tab">Opening Spring 2019</div>
  <p class="ranking">America's #17 Family Resort Tennessee's Only Ranked Resort</p>

  <div class="contact-band">
    <div class="brand"><span class="brand__mark"></span>The Lodge</div>
    <div class="contact">
      <p class="contact__label">Contact:</p>
      <p class="contact__name">Dale Fenton | 865-555-0172</p>
      <p class="contact__email">Dale@bluecedarretreats.example</p>
    </div>
  </div>
</section>

<section class="page page--back">
  <article class="unit unit--galley">
    <span class="unit__number">1</span>
    <div class="floor-plan" role="img" aria-label="Floor plan of the 1 bedroom bunk suite with galley kitchen"></div>
    <div class="unit__details">
      <h2 class="unit__title">1 Bedroom Bunk Suite<br>(Galley Kitchen)</h2>
      <p class="unit__price">$199,000 : Sleeps 6</p>
      <ul class="unit__features">
        <li>Private King Master Bedroom</li>
        <li>Bunk Bed Galley</li>
        <li>Granite Counters Throughout</li>
        <li>Fully Furnished with Custom Furnishings</li>
        <li>Private Balcony</li>
        <li>Equipped Galley Kitchen</li>
        <li>In Unit Laundry</li>
        <li>Queen Sleeper Sofa</li>
      </ul>
    </div>
  </article>

  <article class="unit unit--full">
    <span class="unit__number">1</span>
    <div class="floor-plan" role="img" aria-label="Floor plan of the 1 bedroom bunk suite with full kitchen"></div>
    <div class="unit__details">
      <h2 class="unit__title">1 Bedroom Bunk Suite<br>(Full Kitchen)</h2>
      <p class="unit__price">$209,000; Sleeps 6</p>
      <ul class="unit__features">
        <li>Private King Master Bedroom</li>
        <li>Bunk Bed Galley</li>
        <li>Granite Counters throughout</li>
        <li>Equipped Full Kitchen</li>
        <li>Completely Furnished with Custom Furnishings</li>
        <li>Private Balcony</li>
        <li>In Unit Laundry</li>
        <li>Queen Sleeper Sofa</li>
      </ul>
    </div>
  </article>

  <article class="unit unit--two">
    <span class="unit__number">2</span>
    <div class="floor-plan" role="img" aria-label="Floor plan of the 2 bedroom bunk suite with full kitchen"></div>
    <div class="unit__details">
      <h2 class="unit__title">2 Bedroom Bunk Suite<br>(Full Kitchen)</h2>
      <p class="unit__price">$249,000; Sleeps 10</p>
      <ul class="unit__features">
        <li>Private King Master Bedroom<br>with On-Suite Bathroom</li>
        <li>Two Queen Bedroom</li>
        <li>Bunk Bed Galley</li>
        <li>Granite Counters Throughout</li>
        <li>Full Kitchen</li>
        <li>Completely Furnished with Custom Furnishings</li>
        <li>Private Balcony</li>
        <li>In Unit Laundry</li>
        <li>Queen Sleeper Sofa</li>
      </ul>
    </div>
  </article>
</section>

</body>
</html>
```